My project benefits Military, First Responders, Police, Fire, and Educators.

Contact Information for Business Card

2 Sided appointment card. Visual side will have my head shot with "Brisk Lantern" in a bold graffic/text. I am picturing maybe the headshot applied to a filter that has a matrix effect where the picture is made up of data/numbers flowing vertically through the photo. I am of course open to other concepts as well. Side two will have contact info presented in an attractive visual complimenting the front.

```html
<!DOCTYPE html>
<html lang="en">
<head>
<meta charset="utf-8">
<title>Brisk Lantern — Appointment Card</title>
<link href="https://fonts.googleapis.com/css2?family=Open+Sans:wght@400;600;700;800&display=swap" rel="stylesheet">
<style>
  :root{
    --page:#e9e6e2;
    --ink:#1c1c1c;
    --band:#1b1b1b;
    --red:#c4161c;
    --paper:#ffffff;
    --rule:#3a3a3a;
    --rule-soft:#9a9a9a;
    --panel:#4a3a31;
    --light:#ffffff;
    --ghost:#f6dede;
  }
  *{box-sizing:border-box;margin:0;padding:0}
  html,body{width:1200px;height:900px;overflow:hidden}
  body{background:var(--page);font-family:"Open Sans",Arial,sans-serif;position:relative}

  .card{position:absolute;left:250px;width:700px;height:400px;overflow:hidden;
        box-shadow:0 6px 18px rgba(0,0,0,.18)}
  .card--appointment{top:25px;background:var(--paper)}
  .card--contact{top:465px;background:var(--panel)}

  /* appointment side */
  .appt-band{height:130px;background:var(--band);display:flex;align-items:center;justify-content:center;gap:14px}
  .brand{font-weight:800;letter-spacing:2px;text-transform:uppercase;line-height:1}
  .brand--red{color:var(--red);font-size:46px}
  .brand-dot{width:34px;height:34px;border-radius:50%;background:var(--red)}
  .appt-ghost{position:absolute;left:260px;top:150px;width:180px;height:180px;border-radius:50%;background:var(--ghost);opacity:.55}
  .appt-body{position:relative;padding:20px 70px 0}
  .appt-kicker{text-align:center;font-size:17px;color:var(--ink);letter-spacing:1px}
  .appt-title{font-size:34px;color:var(--red);font-weight:400;margin-top:2px;margin-left:60px}
  .appt-line{height:1px;background:var(--rule);margin-top:8px}
  .appt-line--soft{background:var(--rule-soft);margin-top:40px}
  .appt-line--first{margin-top:-8px;margin-left:300px}
  .appt-line--mid{margin-top:50px}
  .appt-note{text-align:center;font-weight:700;font-size:15px;color:var(--ink);margin-top:16px}

  /* contact side */
  .portrait{position:absolute;left:0;top:0;width:420px;height:400px;
            background:linear-gradient(160deg,#5b4434 0%,#3e2f26 45%,#1f2a44 80%,#17203a 100%)}
  .contact-panel{position:absolute;left:420px;top:0;width:280px;height:400px;padding:50px 22px 0 22px;color:var(--light);text-align:right}
  .contact-brand{display:flex;align-items:center;justify-content:flex-end;gap:10px}
  .brand--light{color:var(--light);font-size:34px}
  .brand-dot--light{width:26px;height:26px;border-radius:50%;background:var(--light)}
  .person-name{margin-top:70px;font-weight:700;font-size:18px;text-transform:uppercase}
  .person-role{font-size:14px;margin-top:2px}
  .contact-list{list-style:none;margin-top:12px;font-size:15px;line-height:1.75}
  .contact-list li{display:flex;justify-content:flex-end;align-items:center;gap:6px}
  .contact-list svg{width:11px;height:11px;fill:var(--light)}
</style>
</head>
<body>

<section class="card card--appointment">
  <header class="appt-band">
    <span class="brand brand--red">Brisk Lantern</span>
    <span class="brand-dot"></span>
  </header>
  <div class="appt-ghost"></div>
  <div class="appt-body">
    <p class="appt-kicker">Your Next</p>
    <h1 class="appt-title">Appointment :</h1>
    <div class="appt-line appt-line--first"></div>
    <div class="appt-line appt-line--soft"></div>
    <div class="appt-line appt-line--mid"></div>
    <div class="appt-line appt-line--soft"></div>
    <p class="appt-note">Please give 24 hours notice if you need to reschedule your appointment</p>
  </div>
</section>

<section class="card card--contact">
  <div class="portrait" role="img" aria-label="Headshot photo of the managing director in a suit, smiling, against a dark wooden door"></div>
  <div class="contact-panel">
    <div class="contact-brand">
      <span class="brand brand--light">Brisk Lantern</span>
      <span class="brand-dot brand-dot--light"></span>
    </div>
    <p class="person-name">Marcus Hale</p>
    <p class="person-role">Managing Director</p>
    <ul class="contact-list">
      <li>(044)555018273
        <svg viewBox="0 0 10 10"><path d="M1 2c0-1 1-1 2-1l1 2-1 1c1 2 2 3 3 3l1-1 2 1c0 1 0 2-1 2C4 9 1 6 1 2z"/></svg></li>
      <li>hello@brisklantern.com
        <svg viewBox="0 0 10 10"><path d="M0 2h10v6H0z M0 2l5 3 5-3" stroke="#4a3a31" stroke-width=".8"/></svg></li>
      <li>www.brisklantern.com
        <svg viewBox="0 0 10 10"><circle cx="5" cy="5" r="5"/></svg></li>
    </ul>
  </div>
</section>

</body>
</html>
```